Pell Dental Care Small Tote Bag

Pell Dental Care needs an advertisement design for a BrightKart Small Tote Bag. See website "www.pelldental-example.com." See uploaded files for small tote bag design template, color scheme, logos, and photo image of Dr. Pell. Designer may crop photo as necessary.

Target Market(s)

Target market is Adults ages 35 to 80.

Industry/Entity Type

Dental

Font styles to use
Sans Serif

```html
<!DOCTYPE html>
<html lang="en">
<head>
<meta charset="utf-8">
<title>Pell Dental Care – Tote Bag Ad</title>
<link rel="stylesheet" href="https://fonts.googleapis.com/css2?family=Arimo:wght@400;700&display=swap">
<style>
  :root {
    --stage: #e4e4e6;
    --paper: #ffffff;
    --sage: #5b7a6f;
    --sage-dark: #3d5c52;
    --taupe: #8a7565;
    --ink: #3a3a3a;
    --white: #ffffff;
  }
  * { box-sizing: border-box; margin: 0; padding: 0; }
  html, body {
    width: 1200px; height: 900px; overflow: hidden;
    background: var(--stage);
    font-family: "Arimo", Arial, sans-serif;
  }
  .ad {
    position: absolute; left: 200px; top: 60px;
    width: 800px; height: 780px;
    background: var(--paper);
    overflow: hidden;
    box-shadow: 0 2px 8px rgba(0,0,0,.15);
  }
  .ad__band { position: absolute; left: 0; top: 0; width: 800px; height: 780px; }
  .brand {
    position: absolute; left: 42px; top: 108px;
    font-size: 86px; font-weight: 400; color: var(--sage);
    letter-spacing: -1px; line-height: 1;
  }
  .tagline {
    position: absolute; right: 61px; top: 210px;
    font-size: 14px; color: var(--sage-dark);
  }
  .doctor-photo {
    position: absolute; left: 42px; top: 220px;
    width: 320px; height: 505px;
    background: linear-gradient(180deg, #d9dde2 0%, #f3f4f6 45%, #e6e8ec 100%);
  }
  .services {
    position: absolute; left: 394px; top: 304px;
    list-style: none;
  }
  .services li {
    display: flex; align-items: center; gap: 12px;
    height: 45px; font-size: 30px; color: var(--white);
  }
  .services svg { width: 24px; height: 24px; }
  .contact { position: absolute; left: 394px; top: 530px; color: var(--ink); }
  .contact__title { font-size: 32px; font-weight: 400; color: var(--sage-dark); margin-bottom: 10px; }
  .contact__line { display: flex; align-items: center; gap: 10px; font-size: 20px; height: 31px; }
  .contact__line svg { width: 17px; height: 17px; }
  .contact__address { font-size: 18px; line-height: 23px; margin-top: 13px; }
  .slogan-bar {
    position: absolute; left: 0; top: 725px; width: 800px; height: 55px;
    background: var(--sage);
    color: var(--white); font-weight: 700; font-size: 27px;
    display: flex; align-items: center; justify-content: center;
  }
</style>
</head>
<body>
  <main class="ad">
    <svg class="ad__band" viewBox="0 0 800 780" aria-hidden="true">
      <path d="M0 254 Q400 282 800 246 L800 500 Q400 470 0 525 Z" fill="var(--sage)"/>
      <path d="M0 244 Q400 272 800 236" stroke="var(--taupe)" stroke-width="6" fill="none"/>
      <path d="M0 535 Q400 480 800 510" stroke="var(--taupe)" stroke-width="6" fill="none"/>
    </svg>

    <h1 class="brand">Pell Dental Care</h1>
    <p class="tagline">Improving lives one <b>smile</b> at a time</p>

    <div class="doctor-photo" role="img" aria-label="Photo of Dr. Pell in a white coat, arms crossed, smiling"></div>

    <ul class="services">
      <li><svg viewBox="0 0 24 24"><path d="M3 13 L9 19 L21 4" stroke="#fff" stroke-width="2.5" fill="none"/></svg>General&nbsp; Dentistry</li>
      <li><svg viewBox="0 0 24 24"><path d="M3 13 L9 19 L21 4" stroke="#fff" stroke-width="2.5" fill="none"/></svg>Cosmetic Dentistry</li>
      <li><svg viewBox="0 0 24 24"><path d="M3 13 L9 19 L21 4" stroke="#fff" stroke-width="2.5" fill="none"/></svg>Beautiful Dentures</li>
      <li><svg viewBox="0 0 24 24"><path d="M3 13 L9 19 L21 4" stroke="#fff" stroke-width="2.5" fill="none"/></svg>Sedation Dentistry</li>
    </ul>

    <section class="contact">
      <h2 class="contact__title">Contact Us Today!</h2>
      <p class="contact__line">
        <svg viewBox="0 0 24 24"><path d="M6.6 10.8c1.4 2.8 3.8 5.1 6.6 6.6l2.2-2.2c.3-.3.7-.4 1-.2 1.1.4 2.3.6 3.6.6.6 0 1 .4 1 1V20c0 .6-.4 1-1 1C10.6 21 3 13.4 3 4c0-.6.4-1 1-1h3.5c.6 0 1 .4 1 1 0 1.3.2 2.5.6 3.6.1.3 0 .7-.2 1z" fill="var(--taupe)"/></svg>
        (555) 014-2290
      </p>
      <p class="contact__line">
        <svg viewBox="0 0 24 24" fill="none" stroke="var(--taupe)" stroke-width="2"><circle cx="12" cy="12" r="9"/><path d="M3 12h18M12 3c3 3 3 15 0 18M12 3c-3 3-3 15 0 18"/></svg>
        www.pelldental-example.com
      </p>
      <p class="contact__address">Lakeside Medical Plaza,<br>2450 Orchard Road, Ste. #310, Sugar Land<br>TX 77478</p>
    </section>

    <footer class="slogan-bar">Life-Changing Family Dental Care In Sugar Land</footer>
  </main>
</body>
</html>
```